Business Cards for IT Consulting Company (Managed Service Provider)

I am looking to have some business cards printed and would like some designs. We are an IT Consulting company based in Vancouver BC. I would like a nice clean and modern look to the cards. I have uploaded all the versions of my logo so parts can be used as needed. Here is a snippit from our website homepage:

Quillbrook Networks Ltd. is an IT Solutions Partner located in Vancouver BC, Canada. We offer IT solutions and support to customers in the greater Vancouver Area. With expertise in Microsoft platforms, as well as Linux and Mac OSX and over 12 years experience in the IT industry, Quillbrook Networks is dedicated to offering our clients top quality service and products. We take pride in the solutions we offer our customers. The greatest compliment a client can give us is to recommend our services.

Quillbrook Networks Ltd. offers a wide range of IT services from onsite service to remote support and managed service solutions. This allows clients to choose the support path that best suits their company’s needs. Supporting many different sized companies from small to enterprise level over the past 12 years Quillbrook Networks has the experience and expertise needed to ensure things run smoothly. Allowing our clients to focus on doing business.

Revolutionizing the way IT services are delivered.

Quillbrook Networks is dedicated to providing our clients with IT solutions that work and grow with them for years to come. This philosophy helps save money in the long run instead of replacing equipment constantly. Far too often IT solutions are not well thought out and while possibly solving the problem at hand, require replacement due to growth or quality within a very short time frame. Quillbrook Networks takes pride in providing solutions that will last and be able to accommodate growth without the need for replacement.

Industry/Entity Type

Information Technology

Contact Information for Business Card

Quillbrook Networks Ltd.
(Employee Name)
Eml: (Employees Email Address)
Web: quillbrook.me
Ph: 604-555-0148

Font styles to use
Serif
Sans Serif

Requirements
Must have
• The Company logo and company colors.
Nice to have
• - Our tag line: "Revolutionizing IT Services" or "Revolutionizing the way IT services are delivered."
• - Also I really like the idea of nature and technology together blending which is sort of where my logo came from so integrating that somehow onto the business cards would be great.

```html
<!DOCTYPE html>
<html lang="en">
<head>
<meta charset="utf-8">
<title>Quillbrook Networks Business Cards</title>
<link rel="stylesheet" href="https://fonts.googleapis.com/css2?family=Montserrat:wght@500;600&family=Arimo:wght@400;700&display=swap">
<style>
  :root {
    --brand-blue: #1aa6e4;
    --brand-pale: #e6f5fc;
    --slate: #5f6062;
    --ink: #4a4b4d;
    --paper: #ffffff;
    --backdrop: #ece9e4;
  }
  * { box-sizing: border-box; margin: 0; padding: 0; }
  html, body { width: 1200px; height: 950px; overflow: hidden; }
  body {
    background: var(--backdrop);
    display: flex;
    flex-direction: column;
    align-items: center;
    justify-content: center;
    gap: 50px;
    font-family: "Arimo", Arial, sans-serif;
  }
  .card {
    width: 700px;
    height: 400px;
    position: relative;
    overflow: hidden;
    box-shadow: 0 6px 18px rgba(0,0,0,0.18);
  }

  /* Back of card */
  .card-back {
    background: var(--slate);
    display: flex;
    flex-direction: column;
    align-items: center;
    justify-content: center;
  }
  .back-brand {
    display: flex;
    align-items: center;
    gap: 14px;
    margin-top: -20px;
  }
  .brand-square {
    width: 34px; height: 34px;
    border: 4px solid var(--brand-blue);
  }
  .back-brand-name {
    font-family: "Montserrat", Arial, sans-serif;
    font-weight: 600;
    font-size: 30px;
    color: var(--brand-blue);
  }
  .tagline {
    position: absolute;
    bottom: 78px;
    width: 100%;
    text-align: center;
    color: var(--paper);
    font-size: 15px;
    letter-spacing: 0.5px;
  }

  /* Front of card */
  .card-front { background: var(--paper); }
  .side-band {
    position: absolute;
    left: 0; top: 0;
    width: 150px; height: 100%;
    background: var(--brand-blue);
  }
  .band-square {
    position: absolute;
    left: 40px; top: 150px;
    width: 70px; height: 70px;
    border: 5px solid var(--paper);
  }
  .faint-shape {
    position: absolute;
    right: 40px; top: 30px;
    width: 240px; height: 240px;
    border-radius: 50%;
    border: 10px solid var(--brand-pale);
  }
  .company-name {
    position: absolute;
    left: 180px; top: 92px;
    font-family: "Montserrat", Arial, sans-serif;
    font-weight: 600;
    font-size: 34px;
    line-height: 1.1;
    color: var(--brand-blue);
  }
  .person-name {
    position: absolute;
    left: 180px; top: 200px;
    font-family: "Montserrat", Arial, sans-serif;
    font-weight: 600;
    font-size: 21px;
    color: var(--brand-blue);
  }
  .address {
    position: absolute;
    left: 180px; top: 242px;
    font-size: 15px;
    line-height: 1.35;
    color: var(--ink);
  }
  .contact-list {
    position: absolute;
    left: 180px; top: 296px;
    list-style: none;
    font-size: 15px;
    color: var(--ink);
  }
  .contact-list li {
    display: flex;
    align-items: center;
    gap: 10px;
    height: 24px;
  }
  .contact-icon { width: 16px; height: 16px; flex: none; }
</style>
</head>
<body>

  <section class="card card-back" aria-label="Card back">
    <div class="back-brand">
      <span class="brand-square"></span>
      <span class="back-brand-name">Quillbrook Networks</span>
    </div>
    <p class="tagline">Revolutionizing IT Services</p>
  </section>

  <section class="card card-front" aria-label="Card front">
    <div class="faint-shape"></div>
    <div class="side-band"><span class="band-square"></span></div>

    <h1 class="company-name">Quillbrook<br>Networks Ltd.</h1>
    <p class="person-name">Mara Lindqvist</p>
    <p class="address">2716 Alder Crescent<br>Vancouver, BC V5K 0A1</p>

    <ul class="contact-list">
      <li>
        <svg class="contact-icon" viewBox="0 0 16 16" aria-hidden="true">
          <circle cx="8" cy="8" r="8" fill="#1aa6e4"/>
          <path d="M5 4.5 L6.6 4.5 L7.2 6.3 L6.3 7 Q7 8.6 9 9.7 L9.7 8.8 L11.5 9.4 L11.5 11 Q8 11.5 5.5 8.3 Q4.5 6.6 5 4.5 Z" fill="#fff"/>
        </svg>
        604 555 0148
      </li>
      <li>
        <svg class="contact-icon" viewBox="0 0 16 16" aria-hidden="true">
          <circle cx="8" cy="8" r="8" fill="#1aa6e4"/>
          <rect x="4" y="5" width="8" height="6" fill="#fff"/>
          <path d="M4 5 L8 8.3 L12 5" fill="none" stroke="#1aa6e4" stroke-width="1"/>
        </svg>
        mara@quillbrook.me
      </li>
      <li>
        <svg class="contact-icon" viewBox="0 0 16 16" aria-hidden="true">
          <circle cx="8" cy="8" r="8" fill="#1aa6e4"/>
          <circle cx="8" cy="8" r="4" fill="none" stroke="#fff" stroke-width="1.2"/>
          <path d="M4 8 H12 M8 4 Q6 8 8 12 M8 4 Q10 8 8 12" fill="none" stroke="#fff" stroke-width="1"/>
        </svg>
        www.quillbrook.me
      </li>
    </ul>
  </section>

</body>
</html>
```